Business card for Eyelash extension salon in Beverly Hills,California USA

We need new business card for our salon in Beverly Hills. The salon name is 'Lashvera' . We would like to have...Business name: Lashvera Name of person: will provide later Address 4720 N.Alder Crest Ave Beverly Hills , CA 90210 Phone: will provide later (Text only) Web: www.lashverastudio.example Snapgrid icon, Circlebook icon follow us for seasonal campaign and news @lashverastudiolounge Design should look elegant, high-end, clean, simple, cohesive with my brand. Please refer my brand board. Business name color will be metallic bronzy color. Im thinking grey background or white background. Thanks

Target Market(s)

25-35. Gender neutral. People who are in Entertainment business industry.
This is High-end Eyelash extension salon in Beverly Hills

Industry/Entity Type

Beauty Salon

Contact Information for Business Card

Business name: Lashvera
Name of person: will provide later
Address 4720 N.Alder Crest Ave Beverly Hills , CA 90210
Phone: will provide later (Text only)
Web: www.lashverastudio.example
Snapgrid icon, Circlebook icon
follow us for seasonal campaign and news @lashverastudiolounge

Requirements
Must have
• Beautiful, elegant, clean and simple look but very attractive and modern
Should not have
• We don't like too clutter, too busy designs.

```html
<!DOCTYPE html>
<html lang="en">
<head>
<meta charset="utf-8">
<title>Lashvera — Business Card</title>
<link rel="stylesheet" href="https://fonts.googleapis.com/css2?family=Playfair+Display:wght@600&family=Work+Sans:wght@400;600&display=swap">
<style>
  :root {
    --page: #d9d9d9;
    --card: #1c1b1b;
    --bronze: #a97a58;
    --bronze-soft: #8f6548;
    --ink: #f4f1ee;
    --shadow: rgba(0, 0, 0, 0.28);
  }
  * { margin: 0; padding: 0; box-sizing: border-box; }
  html, body { width: 1200px; height: 800px; overflow: hidden; }
  body {
    background: var(--page);
    position: relative;
    font-family: "Work Sans", Arial, sans-serif;
  }
  .card {
    position: absolute;
    width: 620px;
    height: 354px;
    background: var(--card);
    border-radius: 22px;
    box-shadow: 0 14px 34px var(--shadow);
  }

  /* Brand side */
  .card--brand { left: 500px; top: 40px; }
  .brand-handle {
    position: absolute;
    left: 52px;
    top: 158px;
    font-size: 15px;
    font-weight: 600;
    color: var(--bronze-soft);
    letter-spacing: 0.2px;
  }
  .brand-name {
    position: absolute;
    right: 58px;
    top: 136px;
    font-size: 64px;
    font-weight: 400;
    color: var(--bronze);
    letter-spacing: 1px;
  }

  /* Contact side */
  .card--contact { left: 80px; top: 412px; }
  .contact {
    position: absolute;
    inset: 0;
    display: flex;
    flex-direction: column;
    align-items: center;
    padding-top: 70px;
    color: var(--ink);
  }
  .contact-name {
    font-family: "Playfair Display", Georgia, serif;
    font-weight: 600;
    font-size: 26px;
    letter-spacing: 3px;
    text-transform: uppercase;
    color: var(--bronze);
  }
  .contact-rule {
    width: 96px;
    height: 1.5px;
    background: var(--bronze);
    margin: 22px 0 20px;
  }
  .contact-phone {
    font-size: 21px;
    font-weight: 600;
    letter-spacing: 1.5px;
    margin-bottom: 10px;
  }
  .contact-line {
    font-size: 19px;
    letter-spacing: 0.8px;
    line-height: 1.45;
  }
  .contact-line .accent { color: var(--bronze); }
  .contact-social {
    display: flex;
    align-items: center;
    gap: 12px;
    margin-top: 8px;
  }
  .social-mark {
    width: 16px;
    height: 16px;
    border-radius: 4px;
    background: var(--bronze);
  }
  .social-label {
    font-size: 13px;
    letter-spacing: 0.8px;
    color: var(--bronze);
  }
</style>
</head>
<body>

  <section class="card card--brand" aria-label="Card front">
    <p class="brand-handle">@lashverastudiolounge</p>
    <p class="brand-name">Lashvera</p>
  </section>

  <section class="card card--contact" aria-label="Card back">
    <div class="contact">
      <h1 class="contact-name">Marisol Quenby</h1>
      <div class="contact-rule"></div>
      <p class="contact-phone">(555) 0148 2236</p>
      <p class="contact-line">marisol@quenbyco.example</p>
      <p class="contact-line">www.<span class="accent">lashverastudio</span>.example</p>
      <div class="contact-social">
        <span class="social-mark" aria-hidden="true"></span>
        <span class="social-label">Snapgrid</span>
        <span class="contact-line">@lashverastudiolounge</span>
      </div>
    </div>
  </section>

</body>
</html>
```